Project Overview:
We are looking to create a website for a monthly subscription IPTV service in WordPress. The website should provide a seamless user experience for customers to sign up for the service and manage their account information. We need the following pages: Home Page, Product Page, Sign-Up Page, and Account Information Page.

Home Page:
The Home Page design should be simple and clean, with a dark theme and minimalistic design elements. We would like to include graphics of popular movie shows displayed on multiple devices. The page should highlight the key benefits and features of our service and provide a clear call-to-action for visitors to sign up.

Product Page:
The Product Page should provide detailed information about our subscription tiers and pricing plans. It should highlight the key features of each plan and provide a clear comparison between them. The page should also include a call-to-action button for visitors to sign up.

Sign-Up Page:
The Sign-Up Page is the conversion page where members will sign up for the service. It should collect the following information: Name, Phone Number, Email, Password, and Payment Information. The design should be simple, intuitive, and easy to use. It should highlight the benefits of our service and provide a clear call-to-action for visitors to sign up.

Account Information Page:
The Account Information Page should allow members to view and manage their account details. It should include the following information: Profile Image, Contact Details, Password Management, Payment Information Management, and Membership Expiration Date. The design should be user-friendly, intuitive, and easy to navigate.

Goals: The primary goal of the website is to provide an easy-to-use portal for customers to sign up for the service and manage their account information. The website should be user-friendly and visually appealing to attract potential customers.

Scope: The scope of the project includes designing a home page, a sign-up page, an account information page, and a payment information page. The website should be designed to be responsive and accessible on desktop and mobile devices.

Design Preferences: The design should be clean, modern, and visually appealing. The use of a color palette that is consistent with the brand identity is recommended. The website should be easy to navigate and provide a clear call-to-action for users to sign up for the service.

FYI: The subscription service I am designing a website for is related to an IPTV service. IPTV stands for Internet Protocol Television, which is a digital television broadcasting protocol that uses the internet to deliver TV programs and videos to viewers. The website will allow customers to sign up for the IPTV service and access their account information such as user name and password, membership tier, name, and payment details. Please let me know if you have any further questions, and I would be happy to provide more details. Thank you!

Dear Designers,

Thank you for your participation in our project. After reviewing the designs received so far, we have decided to update the brief to better reflect our needs and preferences. We apologize for any confusion this may cause, but we believe that these changes will result in better design submissions and a more successful project overall.

The updated brief is as follows:

We are looking to create a website for WordPress.

Also, here is the updated Brief.

Project Title: WordPress Website Design for Monthly Subscription IPTV Service

Project Overview:
We are looking to create a website for a monthly subscription IPTV service. The website should provide a seamless user experience for customers to sign up for the service and manage their account information. We need the following pages: Home Page, Product Page, Sign-Up Page, and Account Information Page.

Home Page:

Product Page:

Sign-Up Page:

Account Information Page:

Design Preferences:
We prefer a dark theme with minimalistic design elements and hits of our logo colors. The website should be easy to use and navigate, with clear calls-to-action and simple, intuitive forms. The design should be optimized for mobile devices and load quickly.

We hope that these updates provide you with a clearer understanding of our requirements and preferences. Please let us know if you have any questions or concerns. We look forward to seeing your revised designs.

Thank you again for your participation.
We will guarantee this project as soon as we see something we like that meets the updated requirements.

The website's target audience is individuals who are interested in subscribing to the monthly service.

4 page

• One item for sale and a client profile section.

```html
<!DOCTYPE html>
<html lang="en">
<head>
<meta charset="utf-8">
<title>Voltaro — Unlimited Movies, TV Shows and More</title>
<link rel="stylesheet" href="https://fonts.googleapis.com/css2?family=Antonio:wght@700&family=Bebas+Neue&family=Jost:wght@400;500&display=swap">
<style>
  :root{
    --bg:#0d0c12;
    --bg-alt:#0b0a10;
    --panel:#15141c;
    --panel-soft:#17161e;
    --red:#f20d0d;
    --white:#ffffff;
    --muted:#5c5b63;
    --text:#e9e9ee;
    --num:#3a3940;
  }
  *{box-sizing:border-box;margin:0;padding:0}
  html,body{width:1200px;height:3806px;overflow:hidden;background:var(--bg)}
  body{position:relative;font-family:"Jost",sans-serif;color:var(--text)}
  .display{font-family:"Bebas Neue",sans-serif;font-weight:400;letter-spacing:.3px;color:var(--white)}
  .abs{position:absolute}
  .btn{position:absolute;display:flex;align-items:center;justify-content:center;gap:8px;font-family:"Antonio",sans-serif;font-weight:700;font-size:16px;color:var(--white);background:var(--red);border-radius:3px;letter-spacing:.2px;white-space:nowrap}
  .btn-outline{background:transparent;border:2px solid #cfcfd4}
  .btn-caps{text-transform:uppercase}
  p.body{font-size:15px;line-height:30px;color:var(--text)}

  .brand{position:absolute;display:flex;align-items:center;gap:14px;font-family:"Bebas Neue",sans-serif;color:var(--white);line-height:1}
  .brand-mark{background:var(--red);border-radius:6px}

  .hero{position:absolute;left:0;top:0;width:1200px;height:636px;overflow:hidden;
    background:linear-gradient(100deg,#1a1e2e 0%,#263048 45%,#3a4258 70%,#2a2e3e 100%)}
  .hero-screens{position:absolute;left:380px;top:0;width:820px;height:636px;
    background:linear-gradient(160deg,#3b5a86 0%,#2c3e5e 35%,#1d2638 70%,#151825 100%);opacity:.75}
  .hero-shade{position:absolute;inset:0;background:linear-gradient(90deg,rgba(18,20,32,.95) 0%,rgba(18,20,32,.6) 45%,rgba(18,20,32,.1) 100%)}
  .hero-watermark{position:absolute;left:450px;top:410px;font-family:"Bebas Neue",sans-serif;font-size:260px;line-height:1;color:rgba(255,255,255,.09);letter-spacing:4px}
  .hero h1{position:absolute;left:110px;top:246px;font-size:62px;line-height:80px}
  .menu-icon{position:absolute;left:952px;top:26px;width:22px;height:22px}

  .section-title{position:absolute;font-size:40px;line-height:1}
  .poster{position:absolute;top:814px;width:130px;height:190px;border-radius:2px}
  .arrow{position:absolute;width:14px;height:14px}

  .faq-item{position:absolute;left:214px;width:801px;height:73px;border-radius:37px;background:var(--panel-soft)}
  .faq-num{position:absolute;left:5px;top:8px;width:57px;height:57px;border-radius:50%;background:var(--num);display:flex;align-items:center;justify-content:center;font-family:"Antonio",sans-serif;font-weight:700;font-size:24px;color:var(--white)}
  .faq-item.open .faq-num{background:var(--red)}
  .faq-q{position:absolute;left:89px;top:21px;font-family:"Antonio",sans-serif;font-weight:700;font-size:21px;color:var(--white);line-height:30px;white-space:nowrap}
  .faq-toggle{position:absolute;right:32px;top:29px;width:16px;height:16px}
  .faq-answer{position:absolute;left:307px;top:2946px;width:660px;border-left:2px solid var(--red);padding-left:17px}
  .faq-answer p{font-size:15px;line-height:26px;color:var(--text)}

  .newsletter{position:absolute;left:112px;top:3192px;width:977px;height:240px;border-radius:26px;background:var(--panel)}
  .email-field{position:absolute;left:529px;top:60px;width:414px;height:54px;border:1px solid #d8d8dc;display:flex;align-items:center;padding-left:28px;font-size:15px;color:var(--text)}

  .social{position:absolute;top:3576px;width:34px;height:34px}
</style>
</head>
<body>

<section class="hero">
  <div class="hero-screens" role="img" aria-label="Wall of glowing TV screens showing film and series stills"></div>
  <div class="hero-shade"></div>
  <div class="hero-watermark" aria-hidden="true">VOLTARO</div>

  <div class="brand" style="left:104px;top:24px;font-size:66px">
    <span class="brand-mark" style="width:34px;height:34px"></span>Voltaro
  </div>

  <svg class="menu-icon" viewBox="0 0 22 22" aria-hidden="true">
    <circle cx="11" cy="11" r="11" fill="rgba(255,255,255,.15)"/>
    <rect x="6" y="7" width="10" height="1.6" fill="#fff"/>
    <rect x="6" y="10.2" width="10" height="1.6" fill="#fff"/>
    <rect x="6" y="13.4" width="10" height="1.6" fill="#fff"/>
  </svg>
  <a class="btn" style="left:998px;top:23px;width:90px;height:34px">Sign Up</a>

  <h1 class="display">Unlimited Movies, TV Shows<br>and More</h1>

  <a class="btn" style="left:112px;top:426px;width:173px;height:43px">
    <svg width="11" height="12" viewBox="0 0 11 12" aria-hidden="true"><path d="M0 0 L11 6 L0 12Z" fill="#fff"/></svg>
    Watch the Trailer
  </a>
  <a class="btn btn-outline btn-caps" style="left:301px;top:426px;width:142px;height:43px">Find Out More</a>
</section>

<h2 class="display section-title" style="left:112px;top:728px">Latest &amp; Trending</h2>
<span class="abs" style="left:1010px;top:742px;font-size:17px;color:var(--muted)">View All</span>

<svg class="arrow" style="left:63px;top:894px" viewBox="0 0 14 14" aria-hidden="true"><path d="M9 2 L4 7 L9 12" stroke="#fff" stroke-width="2" fill="none"/></svg>
<div class="poster" style="left:112px;background:linear-gradient(160deg,#3a6fd0,#c24aa8 55%,#f2a95a)" role="img" aria-label="Space film poster"></div>
<div class="poster" style="left:252px;background:linear-gradient(180deg,#3b2a20,#c86a22 55%,#f5b84a)" role="img" aria-label="War film poster"></div>
<div class="poster" style="left:392px;background:linear-gradient(180deg,#d4d8dc,#8e969e 60%,#3b434a)" role="img" aria-label="Comeback film poster"></div>
<div class="poster" style="left:533px;background:linear-gradient(180deg,#f1ead8,#e25a1e 50%,#b21a12)" role="img" aria-label="Alien film poster"></div>
<div class="poster" style="left:673px;background:linear-gradient(180deg,#f0c27a,#d7553a 55%,#6d7fa8)" role="img" aria-label="Superhero film poster"></div>
<div class="poster" style="left:814px;background:linear-gradient(180deg,#e01820,#b40d16 60%,#6a0a0e)" role="img" aria-label="Crime film poster"></div>
<div class="poster" style="left:954px;background:linear-gradient(180deg,#2b4656,#1d2c36 60%,#2d1a1a)" role="img" aria-label="Horror film poster"></div>
<div class="poster" style="left:1095px;width:105px;border-radius:2px 0 0 2px;background:linear-gradient(180deg,#f6e2dc,#e46a72 55%,#b8323e)" role="img" aria-label="Drama film poster"></div>
<svg class="arrow" style="left:1156px;top:894px" viewBox="0 0 14 14" aria-hidden="true"><path d="M5 2 L10 7 L5 12" stroke="#fff" stroke-width="2" fill="none"/></svg>

<svg class="abs" style="left:196px;top:1202px" width="430" height="430" aria-hidden="true"><circle cx="215" cy="215" r="214" fill="var(--red)"/></svg>
<div class="abs" style="left:139px;top:1198px;width:376px;height:218px;border:3px solid #e6e6ea;background:linear-gradient(180deg,#1b2140,#4a4e6e 55%,#262836)" role="img" aria-label="Laptop screen showing the streaming app home page, with a phone held in front playing a video"></div>
<div class="abs" style="left:285px;top:1404px;width:188px;height:136px;border:3px solid #fff;border-radius:6px;background:linear-gradient(180deg,#8a8c98,#d8cbb8 55%,#3a3a44)" role="img" aria-label="Tablet showing a film page"></div>
<div class="abs" style="left:489px;top:1355px;width:111px;height:228px;border:4px solid #f2f2f4;border-radius:16px;background:linear-gradient(180deg,#1c2433,#0e1118)" role="img" aria-label="Phone showing the streaming app splash screen"></div>

<h2 class="display section-title" style="left:643px;top:1276px;font-size:41px">Watch Everywhere</h2>
<p class="body abs" style="left:643px;top:1336px;width:460px">Lorem ipsum dolor sit amet, consectetur adipiscing elit, sed do eiusmod tempor incididunt ut labore et dolore magna aliqua. Quis ipsum suspendisse ultrices gravida. Risus commodo viverra maecenas accumsan lacus vel facilisis.</p>
<a class="btn" style="left:643px;top:1488px;width:121px;height:42px">Subscribe</a>

<div class="abs" style="left:0;top:1714px;width:1200px;height:2092px;background:var(--bg-alt)"></div>
<h2 class="display section-title" style="left:120px;top:1916px;line-height:53px;font-size:41px">Download Your Shows to<br>Watch Offline.</h2>
<p class="body abs" style="left:120px;top:2030px;width:470px">Lorem ipsum dolor sit amet, consectetur adipiscing elit, sed do eiusmod tempor incididunt ut labore et dolore magna aliqua. Quis ipsum suspendisse ultrices gravida.</p>
<a class="btn" style="left:118px;top:2150px;width:121px;height:43px">Sign Up</a>
<svg class="abs" style="left:598px;top:1822px" width="420" height="420" aria-hidden="true"><circle cx="208" cy="208" r="207" fill="var(--red)"/></svg>
<div class="abs" style="left:675px;top:1957px;width:413px;height:293px;border:3px solid #fff;border-radius:14px;background:linear-gradient(135deg,#8d6a58,#3c3a44 45%,#b57b6a)" role="img" aria-label="Person holding a tablet browsing downloaded shows"></div>

<h2 class="display" style="position:absolute;left:0;top:2448px;width:1200px;text-align:center;font-size:40px;line-height:1">Frequently Asked Questions</h2>

<div class="faq-item" style="top:2548px">
  <span class="faq-num">01</span><span class="faq-q">Lorem ipsum dolor sit amet, consectetur adipiscing elit</span>
  <svg class="faq-toggle" viewBox="0 0 16 16" aria-hidden="true"><path d="M8 1V15M1 8H15" stroke="#55545c" stroke-width="2"/></svg>
</div>
<div class="faq-item" style="top:2651px">
  <span class="faq-num">02</span><span class="faq-q">Lorem ipsum dolor sit amet, consectetur adipiscing elit</span>
  <svg class="faq-toggle" viewBox="0 0 16 16" aria-hidden="true"><path d="M8 1V15M1 8H15" stroke="#55545c" stroke-width="2"/></svg>
</div>
<div class="faq-item" style="top:2755px">
  <span class="faq-num">03</span><span class="faq-q">Lorem ipsum dolor sit amet, consectetur adipiscing elit</span>
  <svg class="faq-toggle" viewBox="0 0 16 16" aria-hidden="true"><path d="M8 1V15M1 8H15" stroke="#55545c" stroke-width="2"/></svg>
</div>
<div class="faq-item open" style="top:2851px">
  <span class="faq-num">04</span><span class="faq-q">Lorem ipsum dolor sit amet, consectetur adipiscing elit</span>
  <svg class="faq-toggle" viewBox="0 0 16 16" aria-hidden="true"><path d="M1 8H15" stroke="var(--red)" stroke-width="2"/></svg>
</div>
<div class="faq-answer">
  <p>Lorem ipsum dolor sit amet, consectetur adipiscing elit, sed do eiusmod tempor incididunt ut labore et dolore magna aliqua. Quis ipsum suspendisse ultrices gravida. Risus commodo viverra maecenas accumsan lacus vel facilisis.</p>
  <p style="margin-top:25px">Lorem ipsum dolor sit amet, consectetur adipiscing elit, sed do eiusmod tempor incididunt ut labore et dolore magna aliqua.</p>
</div>

<section class="newsletter">
  <h2 class="display" style="position:absolute;left:30px;top:56px;font-size:40px;line-height:1">Subscribe to Newsletter</h2>
  <p style="position:absolute;left:33px;top:106px;width:450px;font-size:15px;line-height:25px">Lorem ipsum dolor sit amet, consectetur adipiscing elit, sed do eiusmod tempor</p>
  <div class="email-field">Your Email Address</div>
  <a class="btn btn-caps" style="left:529px;top:134px;width:139px;height:52px">Subscribe</a>
</section>

<footer>
  <div class="brand" style="left:113px;top:3522px;font-size:66px">
    <span class="brand-mark" style="width:34px;height:34px"></span>Voltaro
  </div>
  <p class="abs" style="left:111px;top:3612px;width:640px;font-size:15px;line-height:26px;color:var(--text)">Lorem ipsum dolor sit amet, consectetur adipiscing elit, sed do eiusmod tempor incididunt ut labore et dolore magna aliqua. Quis ipsum suspendisse ultrices gravida. Risus commodo viverra maecenas accumsan lacus vel facilisis.</p>
  <p class="abs" style="left:111px;top:3722px;font-size:15px;color:var(--text)">©Copyrights 2023 Voltaro &nbsp;&nbsp;| &nbsp;&nbsp;All Rights Reserved</p>

  <span class="display abs" style="left:897px;top:3530px;font-size:16px">Connect With Us</span>
  <span class="social" style="left:898px;background:var(--red)" aria-label="Social profile"></span>
  <span class="social" style="left:947px;background:#1d1c24" aria-label="Social profile"></span>
</footer>

</body>
</html>
```